Crestline Plaque & Medal Unique Business Card Design

Recently selected a new logo design and waiting to recieve print files. I've attached image for your review. We are a trophies and awards company that provides engraving on trophies, plaques, name plates, name tags, desk sets, medals, acrylics, and signage.

We are located in Monroe, Louisiana and provide this service with computerized & laser engraving equipment.

Target Market(s)

Corporate, Sport, Church, and Special Events

Industry/Entity Type

Business

Contact Information for Business Card

I'd like to see the following list on the card: Trophies, Plaques, Name Plates, Name Tags, Desk Sets, Medals, Certificates... this is accomplished with Computerized & Laser Engraving

Colors
0555a3
ec1f27
ffffff

Requirements
Must have
• I like either single or double sided. If a design can be created with a frosted card stock I'd consider single. Must be Red, White, and Blue. Dwight Palmer - Owner, 412 W 8th Ave, Monroe, La 71208 office 318-555-0148 fax 318-555-0163 email: info@crestlineplaquemedal.example, and website: www.crestlineplaquemedal.example

```html
<!DOCTYPE html>
<html lang="en">
<head>
<meta charset="utf-8">
<title>Crestline Plaque &amp; Medal – Business Card</title>
<link rel="stylesheet" href="https://fonts.googleapis.com/css2?family=Open+Sans:wght@400;600;700&display=swap">
<style>
  :root {
    --stage: #e6e7ea;
    --card-white: #f7f7f7;
    --brand-blue: #2f56c6;
    --brand-blue-deep: #1f44ad;
    --logo-blue: #1d8fd0;
    --brand-red: #ec1f27;
    --ink-white: #ffffff;
  }
  * { box-sizing: border-box; margin: 0; padding: 0; }
  html, body {
    width: 1200px; height: 818px; overflow: hidden;
    background: var(--stage);
    font-family: "Open Sans", Arial, sans-serif;
  }
  .card {
    position: absolute; left: 110px; top: 129px;
    width: 980px; height: 560px;
    background: var(--card-white);
    box-shadow: 0 10px 30px rgba(0,0,0,.18);
    overflow: hidden;
  }
  .card__brand {
    position: absolute; left: 0; top: 0; width: 100%; height: 250px;
    display: flex; flex-direction: column; align-items: center; justify-content: center;
  }
  .brand-lockup { display: flex; align-items: center; gap: 22px; }
  .brand-lockup__dot {
    width: 34px; height: 34px; border-radius: 50%; background: var(--brand-red);
  }
  .brand-lockup__name {
    font-weight: 700; font-size: 62px; color: var(--logo-blue); letter-spacing: .5px;
  }
  .brand-rule {
    width: 720px; height: 3px; background: var(--logo-blue); margin-top: 14px;
  }
  .card__band {
    position: absolute; left: 0; top: 250px; width: 100%; height: 310px;
    background: linear-gradient(180deg, var(--brand-blue), var(--brand-blue-deep));
    color: var(--ink-white);
    display: flex; padding: 40px 60px 0 70px;
  }
  .contact { width: 430px; }
  .contact__name { font-weight: 700; font-size: 40px; line-height: 1.1; }
  .contact__title { font-size: 26px; margin-bottom: 22px; }
  .contact__line { display: flex; align-items: center; gap: 14px; font-size: 25px; line-height: 40px; }
  .contact__icon { width: 24px; height: 24px; flex: none; }
  .divider { width: 2px; height: 210px; background: var(--ink-white); margin: 8px 44px 0 0; opacity: .9; }
  .services { list-style: none; font-size: 27px; line-height: 36px; }
</style>
</head>
<body>
  <article class="card">
    <header class="card__brand">
      <div class="brand-lockup">
        <span class="brand-lockup__dot"></span>
        <span class="brand-lockup__name">Crestline Plaque &amp; Medal</span>
      </div>
      <div class="brand-rule"></div>
    </header>

    <section class="card__band">
      <div class="contact">
        <p class="contact__name">Employee Name</p>
        <p class="contact__title">Managing Director</p>
        <p class="contact__line">
          <svg class="contact__icon" viewBox="0 0 24 24"><rect width="24" height="24" rx="3" fill="#fff"/><path d="M8 5l2 4-2 1.5c1 2.5 3 4.5 5.5 5.5L15 14l4 2-1 3c-7 0-13-6-13-13z" fill="#2f56c6"/></svg>
          0012 3456 789
        </p>
        <p class="contact__line">
          <svg class="contact__icon" viewBox="0 0 24 24"><rect width="24" height="24" rx="3" fill="#fff"/><rect x="4" y="7" width="16" height="11" fill="none" stroke="#2f56c6" stroke-width="2"/><path d="M4 7l8 6 8-6" fill="none" stroke="#2f56c6" stroke-width="2"/></svg>
          info@youremail.com
        </p>
        <p class="contact__line">
          <svg class="contact__icon" viewBox="0 0 24 24"><rect width="24" height="24" rx="3" fill="#fff"/><circle cx="12" cy="12" r="7" fill="none" stroke="#2f56c6" stroke-width="1.8"/><ellipse cx="12" cy="12" rx="3" ry="7" fill="none" stroke="#2f56c6" stroke-width="1.5"/><path d="M5 12h14" stroke="#2f56c6" stroke-width="1.5"/></svg>
          www.yourwebsite.com
        </p>
      </div>
      <div class="divider"></div>
      <ul class="services">
        <li>engraving on trophies</li>
        <li>plaques</li>
        <li>name plates</li>
        <li>name tags, desk sets</li>
        <li>medals</li>
        <li>acrylics and signage</li>
      </ul>
    </section>
  </article>
</body>
</html>
```